Business card for medical clinic

I need an upmarket, modern medical/health business card for my clinic

Contact Information for Business Card

name, address, email, qr code

```html
<!DOCTYPE html>
<html lang="en">
<head>
<meta charset="utf-8">
<title>Meridian Care Clinic – Business Card</title>
<link rel="stylesheet" href="https://fonts.googleapis.com/css2?family=Poppins:wght@300;400;500;700&display=swap">
<style>
  :root {
    --stage: #232323;
    --card: #202023;
    --card-deep: #1b1b1e;
    --accent: #1d9ad6;
    --accent-soft: #2a7fb8;
    --ink-light: #ffffff;
    --divider: #1d7fb3;
  }
  * { margin: 0; padding: 0; box-sizing: border-box; }
  html, body {
    width: 1200px; height: 711px; overflow: hidden;
    background: var(--stage);
    font-family: "Poppins", sans-serif;
  }
  .stage {
    position: relative; width: 1200px; height: 711px;
    display: flex; align-items: center; justify-content: center; gap: 40px;
  }
  .card {
    position: relative; width: 540px; height: 310px;
    border-radius: 22px;
    background: var(--card);
    border-bottom: 5px solid var(--accent);
    border-left: 3px solid var(--accent);
    box-shadow: 0 14px 28px rgba(0,0,0,.55);
    overflow: hidden;
  }
  /* Front */
  .card-front__pattern {
    position: absolute; inset: 0;
    background: radial-gradient(ellipse at 70% 25%, #3a3a3e 0%, #26262a 45%, var(--card-deep) 100%);
  }
  .brand {
    position: absolute; display: flex; align-items: center; gap: 14px;
    font-weight: 500; letter-spacing: .08em; text-transform: uppercase; white-space: nowrap;
  }
  .brand__dot {
    width: 46px; height: 46px; border-radius: 50%;
  }
  .card-front .brand { left: 50%; top: 50%; transform: translate(-50%, -50%); color: var(--ink-light); font-size: 26px; }
  .card-front .brand__dot { background: var(--ink-light); }

  /* Back */
  .card-back .brand { left: 28px; top: 140px; color: var(--accent); font-size: 15px; gap: 10px; }
  .card-back .brand__dot { width: 30px; height: 30px; background: var(--accent); }
  .card-back__divider {
    position: absolute; left: 262px; top: 40px; width: 1px; height: 230px;
    background: var(--divider);
  }
  .contact { position: absolute; left: 290px; top: 52px; width: 240px; }
  .contact__name { font-size: 30px; line-height: 1; color: var(--accent); white-space: nowrap; }
  .contact__name strong { font-weight: 700; }
  .contact__name span { font-weight: 300; }
  .contact__role { margin-top: 6px; font-size: 13px; font-weight: 500; color: var(--ink-light); }
  .contact__address { margin-top: 18px; font-size: 13px; line-height: 1.45; color: var(--accent); }
  .contact__list { margin-top: 16px; list-style: none; }
  .contact__item {
    display: flex; align-items: center; gap: 9px;
    font-size: 13px; line-height: 1.9; color: var(--ink-light);
  }
  .contact__icon { width: 14px; height: 14px; flex: none; }
</style>
</head>
<body>
<main class="stage">
  <section class="card card-front">
    <div class="card-front__pattern" role="img" aria-label="Embossed repeating pattern of small glossy marks across the card"></div>
    <div class="brand">
      <span class="brand__dot"></span>
      <span class="brand__name">Meridian Care Clinic</span>
    </div>
  </section>

  <section class="card card-back">
    <div class="brand">
      <span class="brand__dot"></span>
      <span class="brand__name">Meridian Care Clinic</span>
    </div>
    <div class="card-back__divider"></div>
    <div class="contact">
      <h1 class="contact__name"><strong>Marta</strong> <span>Velenko</span></h1>
      <p class="contact__role">Founder &amp; CEO</p>
      <p class="contact__address">1840 Linden Ave. Suite 310<br>Austin, TX 78701</p>
      <ul class="contact__list">
        <li class="contact__item">
          <svg class="contact__icon" viewBox="0 0 24 24" fill="var(--accent)"><path d="M6.6 10.8a15 15 0 0 0 6.6 6.6l2.2-2.2a1 1 0 0 1 1-.25 11.4 11.4 0 0 0 3.6.57 1 1 0 0 1 1 1V20a1 1 0 0 1-1 1A17 17 0 0 1 3 4a1 1 0 0 1 1-1h3.5a1 1 0 0 1 1 1c0 1.25.2 2.45.57 3.57a1 1 0 0 1-.25 1z"/></svg>
          (512) 555-0147
        </li>
        <li class="contact__item">
          <svg class="contact__icon" viewBox="0 0 24 24" fill="none" stroke="var(--accent)" stroke-width="2"><circle cx="12" cy="12" r="9"/><path d="M3 12h18M12 3c3 3.5 3 14.5 0 18M12 3c-3 3.5-3 14.5 0 18"/></svg>
          info@yourwebsite.com
        </li>
        <li class="contact__item">
          <svg class="contact__icon" viewBox="0 0 24 24" fill="none" stroke="var(--accent)" stroke-width="2"><rect x="3" y="6" width="18" height="13" rx="1"/><path d="M3 7l9 7 9-7"/></svg>
          www.yourwebsite.com
        </li>
      </ul>
    </div>
  </section>
</main>
</body>
</html>
```